A weight loss and fitness website design

I am into different types of modern weight loss techniques for people who are a little fatty and wish to be physically and mentally fit. Basically, the website is to teach people how to reduce weight using different methods such as diet, exercises, yoga and other forms. I would need an eye catching website which would make visitors want to come back. The will be also be different forms of exercises for a health and fit life. This said, my website is to have two categories of
1) weight loss techniques
2) exercise of fit and healthy living.
I prefer bright colors such as green, blue, yellow, and orange. Imagery should include before and after pictures of people suffering from obesity, people under going exercises.
Designers can get ideas and inspiration from the website fitlumen.com which i was previously part of the team.
Target Market(s)
My target audience are people suffering from obesity, malnutrition and physical deficiency.
Industry/Entity Type
Fitness
Coding
Coded - Design and coding required
Number of Pages Required
1 page
Look and feel

```html
<!DOCTYPE html>
<html lang="en">
<head>
<meta charset="utf-8">
<title>Trimwell Fitness</title>
<link rel="stylesheet" href="https://fonts.googleapis.com/css2?family=Open+Sans:wght@400;600;700&display=swap">
<style>
:root{
  --blue:#1f8fdc;
  --blue-dark:#1479c4;
  --blue-deep:#0f6db3;
  --green:#72bd2e;
  --green-dark:#5aa51f;
  --ink:#333a40;
  --muted:#7b848b;
  --white:#ffffff;
  --footer:#16191c;
  --photo-warm:#d8c7b8;
  --photo-cool:#b9c9d6;
}
*{box-sizing:border-box;margin:0;padding:0}
html,body{width:1200px;height:3764px;overflow:hidden}
body{font-family:"Open Sans",Arial,sans-serif;color:var(--ink);background:var(--white);position:relative}
section,header,footer{position:absolute;left:0;width:1200px}
.photo{display:block}

/* header */
.site-header{top:0;height:88px;background:var(--white);box-shadow:0 2px 6px rgba(0,0,0,.08);z-index:2}
.brand{position:absolute;left:24px;top:22px;font-size:32px;font-weight:700;color:var(--blue)}
.nav{position:absolute;right:40px;top:0;display:flex;height:88px;align-items:center;gap:30px;list-style:none}
.nav li{font-size:13px;font-weight:600;color:var(--ink);letter-spacing:.5px}
.nav li.active{color:var(--white);background:var(--blue);padding:32px 18px;position:relative}
.nav li.active::after{content:"";position:absolute;left:50%;bottom:-10px;margin-left:-10px;border:10px solid transparent;border-bottom:0;border-top-color:var(--blue)}

/* hero */
.hero{top:88px;height:512px}
.hero .photo{position:absolute;inset:0;width:100%;height:100%;background:linear-gradient(90deg,#eef0f1 0%,#e6e7e8 45%,#d9d2cc 70%,#c9bcb2 100%)}
.hero h1{position:absolute;left:110px;top:180px;font-size:50px;font-weight:600;color:#3b4248;letter-spacing:1px}
.hero p{position:absolute;left:110px;top:255px;width:460px;font-size:14px;line-height:22px;color:var(--muted)}
.hero .more{position:absolute;left:110px;top:350px;color:var(--green)}
.dots{position:absolute;left:660px;top:470px;display:flex;gap:8px}
.dots span{width:12px;height:12px;border-radius:50%;background:#c9cdd0}
.dots span:first-child{background:var(--blue)}

.more{display:flex;align-items:center;gap:8px;font-size:14px;font-weight:600;letter-spacing:.5px}
.more::before{content:"";width:18px;height:18px;border-radius:50%;background:currentColor;
  -webkit-mask:radial-gradient(circle,transparent 0,transparent 0) ;}
.more .arrow{display:none}

/* shared titles */
.section-title{position:absolute;left:0;width:1200px;text-align:center;font-size:28px;font-weight:600;letter-spacing:1px}
.section-lead{position:absolute;left:150px;width:900px;text-align:center;font-size:13px;line-height:21px}

/* welcome */
.welcome{top:600px;height:300px;background:var(--blue);color:var(--white)}
.welcome .section-title{top:60px}
.welcome .section-lead{top:118px;opacity:.9}
.welcome .more{position:absolute;left:540px;top:210px;color:var(--white)}

/* techniques */
.techniques{top:900px;height:1220px;background:linear-gradient(180deg,var(--blue-dark) 0%,var(--blue) 50%,var(--blue-deep) 100%);color:var(--white);overflow:hidden}
.techniques .backdrop{position:absolute;left:250px;top:250px;width:700px;height:950px;background:radial-gradient(ellipse at center,rgba(255,255,255,.14),rgba(255,255,255,0) 70%)}
.techniques .section-title{top:80px}
.techniques .section-lead{top:135px;opacity:.9}
.split-title{font-size:24px;font-weight:600;letter-spacing:.5px;margin-bottom:16px}
.split-text{font-size:13px;line-height:21px;opacity:.9}
.split{position:absolute;width:1200px;left:0}
.split .copy{position:absolute;width:560px}
.split .more{position:absolute;color:var(--white)}
.split .photo{position:absolute;width:368px;height:210px;border:5px solid var(--white)}
.row-diet{top:240px}
.row-diet .copy{left:112px;top:0}
.row-diet .photo{left:720px;top:0;background:linear-gradient(135deg,#e9eef2,#aab7c2)}
.row-diet .more{left:112px;top:200px}
.row-exercise{top:560px}
.row-exercise .photo{left:112px;top:0;background:linear-gradient(135deg,#b08a6a,#6f5b4e)}
.row-exercise .copy{left:528px;top:30px}
.row-exercise .more{left:528px;top:200px}
.row-yoga{top:900px}
.row-yoga .copy{left:112px;top:0}
.row-yoga .photo{left:720px;top:0;background:linear-gradient(135deg,#c8b29c,#8b7767)}
.row-yoga .more{left:112px;top:200px}

/* training */
.training{top:2120px;height:800px;background:linear-gradient(180deg,var(--green) 0%,#86c63f 55%,var(--green-dark) 100%);color:var(--white);overflow:hidden}
.training .section-title{top:80px}
.training .section-lead{top:133px;opacity:.95}
.row-fit{top:240px}
.row-fit .copy{left:112px;top:0}
.row-fit .photo{left:720px;top:0;background:linear-gradient(135deg,#f1f1f1,#b7c0c7)}
.row-fit .more{left:112px;top:200px}
.row-living{top:540px}
.row-living .photo{left:112px;top:0;background:linear-gradient(135deg,#efe9e4,#c6aa93)}
.row-living .copy{left:528px;top:20px}
.row-living .more{left:528px;top:200px}

/* success */
.success{top:2920px;height:580px;background:var(--white)}
.success .section-title{top:70px;color:#3b4248}
.success .section-lead{top:130px;color:var(--muted)}
.stories{position:absolute;top:280px;left:112px;display:flex;gap:40px}
.story{width:312px;height:220px;position:relative;background:linear-gradient(90deg,#e9e6e3,#d7cdc4);border:1px solid #e2e2e2}
.story .labels{position:absolute;left:0;bottom:0;width:100%;display:flex}
.story .labels span{flex:1;text-align:center;background:var(--blue);color:var(--white);font-size:11px;font-weight:600;padding:6px 0;letter-spacing:.5px}
.story .labels span+span{border-left:1px solid rgba(255,255,255,.5)}

/* footer */
.site-footer{top:3500px;height:220px;background:var(--footer);color:#c7ccd0}
.footer-title{font-size:16px;font-weight:700;color:var(--white);letter-spacing:.5px;margin-bottom:18px}
.links{position:absolute;left:112px;top:36px}
.link-cols{display:flex;gap:70px}
.link-cols ul{list-style:none}
.link-cols li{font-size:12px;line-height:26px;display:flex;align-items:center;gap:8px}
.link-cols li::before{content:"";width:6px;height:6px;border-radius:50%;background:var(--green)}
.newsletter{position:absolute;left:740px;top:36px;width:360px}
.newsletter p{font-size:12px;line-height:19px;margin-bottom:18px}
.signup{display:flex}
.signup .field{flex:1;height:36px;background:#2b3034;border:1px solid #3a4045;color:#8c9399;font-size:12px;padding:9px 12px}
.signup .btn{width:100px;height:36px;background:var(--green);color:var(--white);font-size:12px;font-weight:700;display:flex;align-items:center;justify-content:center}
.bottom-bar{position:absolute;top:3720px;left:0;width:1200px;height:44px;background:var(--blue);color:var(--white);font-size:11px}
.bottom-bar .copyright{position:absolute;left:112px;top:14px}
.social{position:absolute;right:112px;top:11px;display:flex;gap:6px}
.social span{width:22px;height:22px;border-radius:3px;background:rgba(255,255,255,.25)}
</style>
</head>
<body>

<header class="site-header">
  <div class="brand">Trimwell Fitness</div>
  <ul class="nav">
    <li class="active">HOME</li>
    <li>TRAINING</li>
    <li>WEIGHT LOSS</li>
    <li>HEALTHY LIVING</li>
    <li>CONTACT US</li>
    <li>LOGIN</li>
  </ul>
</header>

<section class="hero">
  <div class="photo" role="img" aria-label="Slim waist wrapped in a yellow measuring tape"></div>
  <h1>MODERN WEIGHT LOSS</h1>
  <p>Simple, proven methods to lose weight and stay fit. Learn how small daily steps with food, movement and rest can change the way you look and feel for good.</p>
  <div class="more">READ MORE</div>
  <div class="dots"><span></span><span></span><span></span></div>
</section>

<section class="welcome">
  <h2 class="section-title">WELCOME TO TRIMWELL FITNESS</h2>
  <p class="section-lead">We help people of every size build a stronger body and a calmer mind. Our guides cover eating well, training at home and outdoors, yoga and rest, with clear plans that fit real life. Start today and come back each week to track your progress and find new ideas.</p>
  <div class="more">READ MORE</div>
</section>

<section class="techniques">
  <div class="backdrop" role="img" aria-label="Faint photo of a woman stretching"></div>
  <h2 class="section-title">WEIGHT LOSS TECHNIQUES</h2>
  <p class="section-lead">Choose the method that suits you best. Each technique below comes with easy steps, sample plans and tips from our coaches so you can lose weight safely and keep it off over time.</p>

  <div class="split row-diet">
    <div class="copy">
      <h3 class="split-title">DIET</h3>
      <p class="split-text">Good eating habits are the base of any weight loss plan. Learn to build balanced plates, control portions and pick fresh foods that keep you full for longer. Our simple meal guides show you what to eat at breakfast, lunch and dinner, how to plan snacks and how to enjoy treats without losing track of your goals. Small swaps add up fast.</p>
    </div>
    <div class="photo" role="img" aria-label="Bathroom scale with a measuring tape"></div>
    <div class="more">READ MORE</div>
  </div>

  <div class="split row-exercise">
    <div class="photo" role="img" aria-label="People working out together in a gym"></div>
    <div class="copy">
      <h3 class="split-title">EXERCISES</h3>
      <p class="split-text">Regular movement burns calories, builds muscle and lifts your mood. Our routines start gently and grow with you, from brisk walks and light cardio to strength circuits you can do at home or in the gym. Each session lists sets, rest times and safe form so you can train with confidence at any level.</p>
    </div>
    <div class="more">READ MORE</div>
  </div>

  <div class="split row-yoga">
    <div class="copy">
      <h3 class="split-title">YOGA</h3>
      <p class="split-text">Yoga builds strength, balance and calm in one practice. Gentle flows help loosen stiff joints, while stronger sequences tone the core and legs. Breathing work lowers stress, which helps control cravings. Follow our short daily classes on the mat at home and feel lighter in body and mind within weeks.</p>
    </div>
    <div class="photo" role="img" aria-label="Group yoga class holding a plank pose"></div>
    <div class="more">READ MORE</div>
  </div>
</section>

<section class="training">
  <h2 class="section-title">FITNESS TRAINING</h2>
  <p class="section-lead">Training plans for a fit and healthy life. Find workouts for every level, tips for staying active each day and habits that help you feel your best at home and at work.</p>

  <div class="split row-fit">
    <div class="copy">
      <h3 class="split-title">EXERCISE OF FIT</h3>
      <p class="split-text">Build lasting fitness with a mix of cardio, strength and mobility. Our weekly programs balance hard days with easy ones so your body can recover and grow. Track your reps, time and effort, then step up slowly as you gain power. Stay consistent and the results will follow.</p>
    </div>
    <div class="photo" role="img" aria-label="Woman stretching her leg on a mat"></div>
    <div class="more">READ MORE</div>
  </div>

  <div class="split row-living">
    <div class="photo" role="img" aria-label="Smiling woman holding a glass of water"></div>
    <div class="copy">
      <h3 class="split-title">HEALTHY LIVING</h3>
      <p class="split-text">Health is more than the gym. Drink enough water, sleep well, walk often and take time to rest your mind. Our guides cover daily routines, stress care and simple habits that keep your energy high and your weight steady.</p>
    </div>
    <div class="more">READ MORE</div>
  </div>
</section>

<section class="success">
  <h2 class="section-title">SUCCESS STORIES</h2>
  <p class="section-lead">Real people, real change. See how our members reached their goals with steady work and the right plan, and get inspired to start your own journey today.</p>
  <div class="stories">
    <div class="story" role="img" aria-label="Before and after photos of a man's waist">
      <div class="labels"><span>BEFORE</span><span>AFTER</span></div>
    </div>
    <div class="story" role="img" aria-label="Before and after photos of a woman's waist">
      <div class="labels"><span>BEFORE</span><span>AFTER</span></div>
    </div>
    <div class="story" role="img" aria-label="Before and after photos of a woman's figure">
      <div class="labels"><span>BEFORE</span><span>AFTER</span></div>
    </div>
  </div>
</section>

<footer class="site-footer">
  <div class="links">
    <h4 class="footer-title">QUICK LINKS</h4>
    <div class="link-cols">
      <ul><li>Weight Loss Techniques</li><li>Exercise of Fit</li><li>Healthy Living</li></ul>
      <ul><li>Blog</li><li>Services</li><li>Contact</li></ul>
      <ul><li>Privacy Policy</li><li>Terms &amp; Conditions</li><li>Sitemap</li></ul>
    </div>
  </div>
  <div class="newsletter">
    <h4 class="footer-title">NEWSLETTER SIGNUP</h4>
    <p>Get weekly tips, new workouts and healthy recipes sent straight to your inbox.</p>
    <div class="signup"><div class="field">Email Address</div><div class="btn">SUBMIT</div></div>
  </div>
</footer>
<div class="bottom-bar">
  <div class="copyright">Copyright 2015 Trimwell Fitness. All rights reserved.</div>
  <div class="social"><span></span><span></span><span></span><span></span><span></span></div>
</div>

</body>
</html>
```